BMR Going Cashless

Hello,
We are a medical office looking to get a flyer created to promote to our patients we will be going "Cashless." Our tagline will be "Cash-Less is Stress-Less"

"Starting in July, to offer you the fastest and most convenient service, we are transitioning to a cashless system. You can now enjoy faster checkout times and greater security with card and contactless payments. More info to come."

I've added two other flyers as sample designs we've used.

Please include logo, addresses, website, phone number

Files to include jpeg, png, pdf (under 5mb), Facebook and Instagram sizing.

Thank you,
Lowen

```html
<!DOCTYPE html>
<html lang="en">
<head>
<meta charset="utf-8">
<title>BMR Going Cashless</title>
<link rel="stylesheet" href="https://fonts.googleapis.com/css2?family=League+Spartan:wght@700;800;900&family=Poppins:wght@400;500;600;700&display=swap">
<style>
:root{
  --backdrop:#c4c4c4;
  --paper:#ffffff;
  --mist:#e6e5e3;
  --charcoal:#323232;
  --teal:#52c3a4;
  --teal-soft:#b7e6d8;
  --orange:#f07c4a;
  --pin:#e8394a;
  --ink:#2f2f2f;
}
*{margin:0;padding:0;box-sizing:border-box}
html,body{width:1200px;height:2548px;overflow:hidden}
body{background:var(--backdrop);position:relative;font-family:"Poppins",sans-serif;color:var(--ink)}
.card{position:absolute;background:var(--paper);overflow:hidden;box-shadow:8px 14px 14px rgba(0,0,0,.25)}
.card--square{left:240px;top:144px;width:733px;height:733px}
.card--tall{left:240px;top:1081px;width:735px;height:1308px}
.size-label{position:absolute;width:1200px;text-align:center;font-size:28px;font-weight:500;color:#3a3a3a}
.shapes{position:absolute;left:0;top:0}
.abs{position:absolute;z-index:2}
.headline{font-family:"League Spartan",sans-serif;font-weight:800;line-height:.9;white-space:nowrap;z-index:3}
.headline--dark{color:var(--ink)}
.headline--teal{color:var(--teal);text-shadow:3px 4px 0 var(--paper),6px 7px 0 var(--teal-soft)}
.band{background:var(--orange);color:#fff;font-weight:500;letter-spacing:.22em;display:flex;align-items:center;justify-content:center;border-radius:0 4px 4px 0}
.month{font-family:"League Spartan",sans-serif;font-weight:800;line-height:1}
.lead{border-left:4px solid var(--orange);line-height:1.2}
.benefit{font-weight:700;text-transform:uppercase;line-height:1.3}
.contactless{font-family:"League Spartan",sans-serif;font-weight:800;color:var(--teal);text-transform:uppercase;line-height:1.05}
.website{letter-spacing:.16em;font-weight:500;color:var(--ink)}
.website b{color:var(--orange);font-weight:600}
.photo{z-index:1;background:linear-gradient(155deg,#e4b59a 0%,#cf9d80 30%,#6b6464 55%,#3c3a3a 80%)}
.photo--square{clip-path:polygon(0% 88%,45% 45%,70% 25%,85% 0%,100% 8%,100% 100%,90% 100%,15% 100%)}
.photo--tall{clip-path:polygon(0% 88%,40% 40%,62% 18%,70% 2%,85% 0%,100% 12%,100% 88%,30% 100%,8% 100%)}
.brand{display:flex;align-items:center;gap:10px;color:var(--orange);font-weight:700;white-space:nowrap}
.brand-dot{border-radius:50%;background:var(--teal);flex:none}
.offices{color:#fff}
.office{border-bottom:1px solid #4a4a4a}
.office:last-child{border-bottom:none}
.office-name{color:var(--orange);font-weight:700;display:flex;align-items:center;gap:4px}
.office-addr{font-weight:500;line-height:1.25}
.phone{display:flex;align-items:center;gap:8px;font-weight:600;white-space:nowrap}
</style>
</head>
<body>

<section class="card card--square">
  <svg class="shapes" width="733" height="733" viewBox="0 0 733 733">
    <path fill="var(--mist)" d="M0,495 L30,488 L60,493 L95,484 L130,490 L165,482 L205,488 L245,480 L290,486 L330,478 L370,485 L410,479 L445,486 L445,733 L0,733 Z"/>
    <path fill="var(--charcoal)" d="M428,0 L733,0 L733,733 L438,733 L432,700 L440,665 L430,630 L438,590 L429,550 L437,510 L428,470 L436,430 L427,390 L435,350 L426,310 L434,270 L425,230 L433,190 L424,150 L432,110 L423,70 L431,35 Z"/>
  </svg>

  <div class="abs photo photo--square" role="img" aria-label="Photo of a hand holding a card payment terminal with a card inserted" style="left:290px;top:141px;width:443px;height:283px"></div>

  <div class="abs headline headline--dark" style="left:49px;top:54px;font-size:56px">CASH-LESS IS</div>
  <div class="abs headline headline--teal" style="left:48px;top:108px;font-size:104px">STRESS</div>
  <div class="abs headline headline--teal" style="left:48px;top:193px;font-size:104px">LESS</div>

  <div class="abs band" style="left:0;top:306px;width:257px;height:36px;font-size:22px">STARTING IN</div>
  <div class="abs month" style="left:48px;top:355px;font-size:56px">JULY</div>
  <div class="abs" style="left:182px;top:356px;font-size:21px;font-weight:700;line-height:1">TO OFFER<br>YOU</div>
  <p class="abs lead" style="left:48px;top:410px;width:305px;padding-left:10px;font-size:16.5px">the fastest and most convenient service, we are transitioning to a cashless system</p>

  <svg class="abs" style="left:45px;top:532px" width="44" height="66" viewBox="0 0 44 66" fill="none" stroke="var(--orange)" stroke-width="2.5">
    <rect x="3" y="3" width="38" height="60" rx="4"/><rect x="9" y="10" width="26" height="14"/>
    <path d="M9 31h6M19 31h6M29 31h6M9 39h6M19 39h6M29 39h6M9 47h6M19 47h6M29 47h6M12 63v-8h20v8"/>
  </svg>
  <p class="abs benefit" style="left:105px;top:531px;width:300px;font-size:15.5px">You can now enjoy faster checkout times and greater security with card and</p>
  <div class="abs contactless" style="left:46px;top:610px;font-size:30px;white-space:nowrap">Contactless Payments</div>
  <div class="abs website" style="left:49px;top:664px;font-size:25px">www.<b>bmrfootcare</b>.com</div>

  <div class="abs brand" style="left:470px;top:70px;font-size:22px"><span class="brand-dot" style="width:20px;height:20px"></span>BMR FOOT CARE</div>

  <div class="abs offices" style="left:480px;top:400px;width:215px">
    <div class="office" style="padding:4px 0 8px">
      <div class="office-name" style="font-size:19px"><svg width="12" height="16" viewBox="0 0 12 16"><path fill="var(--pin)" d="M6 0a6 6 0 0 1 6 6c0 4-6 10-6 10S0 10 0 6a6 6 0 0 1 6-6z"/><circle cx="6" cy="6" r="2" fill="#fff"/></svg>Ashford Office</div>
      <div class="office-addr" style="font-size:11.5px;padding-left:3px">210 Oakridge Ave. Suite 120<br>Ashford, MD20000</div>
    </div>
    <div class="office" style="padding:10px 0 8px">
      <div class="office-name" style="font-size:19px"><svg width="12" height="16" viewBox="0 0 12 16"><path fill="var(--pin)" d="M6 0a6 6 0 0 1 6 6c0 4-6 10-6 10S0 10 0 6a6 6 0 0 1 6-6z"/><circle cx="6" cy="6" r="2" fill="#fff"/></svg>Millbrook Office</div>
      <div class="office-addr" style="font-size:11.5px;padding-left:3px">45 Willow Lane<br>Millbrook, WV20001</div>
    </div>
    <div class="office" style="padding:10px 0 8px">
      <div class="office-name" style="font-size:19px"><svg width="12" height="16" viewBox="0 0 12 16"><path fill="var(--pin)" d="M6 0a6 6 0 0 1 6 6c0 4-6 10-6 10S0 10 0 6a6 6 0 0 1 6-6z"/><circle cx="6" cy="6" r="2" fill="#fff"/></svg>Cedarville Office</div>
      <div class="office-addr" style="font-size:11.5px;padding-left:3px">980 Harbor Blvd. Suite 300<br>Cedarville, MD20002</div>
    </div>
  </div>
  <div class="abs phone" style="left:450px;top:657px;font-size:28px;color:#fff">
    <svg width="26" height="26" viewBox="0 0 26 26"><circle cx="13" cy="13" r="13" fill="var(--teal)"/><path fill="#fff" d="M9 6l3 4-2 2c1 2 3 4 5 5l2-2 4 3-2 3c-6 0-12-6-12-12z"/></svg>(555)014-0192
  </div>
</section>
<div class="size-label" style="top:930px">1080 X 1080</div>

<section class="card card--tall">
  <svg class="shapes" width="735" height="1308" viewBox="0 0 735 1308">
    <path fill="var(--mist)" d="M0,545 L30,530 L70,537 L110,524 L150,532 L190,521 L230,530 L270,519 L310,528 L350,518 L400,526 L450,520 L500,528 L735,520 L735,1308 L0,1308 Z"/>
    <path fill="var(--charcoal)" d="M435,660 L735,660 L735,1308 L438,1308 L432,1270 L440,1230 L431,1190 L439,1150 L430,1110 L438,1070 L429,1030 L437,990 L428,950 L436,910 L427,870 L435,830 L426,790 L434,750 L427,710 Z"/>
  </svg>

  <div class="abs photo photo--tall" role="img" aria-label="Photo of a hand holding a card payment terminal with a card inserted" style="left:50px;top:349px;width:685px;height:383px"></div>

  <div class="abs headline headline--dark" style="left:57px;top:60px;font-size:100px">CASH-LESS IS</div>
  <div class="abs headline headline--teal" style="left:55px;top:140px;font-size:190px">STRESS</div>
  <div class="abs headline headline--teal" style="left:55px;top:294px;font-size:190px">LESS</div>

  <div class="abs band" style="left:432px;top:691px;width:250px;height:35px;font-size:23px">STARTING IN</div>
  <div class="abs month" style="left:485px;top:740px;font-size:86px;color:#fff">JULY</div>
  <div class="abs" style="left:486px;top:818px;font-size:28px;font-weight:700;color:var(--teal);font-family:'League Spartan',sans-serif">TO OFFER YOU</div>
  <p class="abs lead" style="left:486px;top:858px;width:215px;padding-left:14px;font-size:21px;color:#fff">the fastest and most convenient service, we are transitioning to a cashless system</p>

  <div class="abs offices" style="left:483px;top:1022px;width:218px">
    <div class="office" style="padding:4px 0 8px">
      <div class="office-name" style="font-size:20px"><svg width="12" height="16" viewBox="0 0 12 16"><path fill="var(--pin)" d="M6 0a6 6 0 0 1 6 6c0 4-6 10-6 10S0 10 0 6a6 6 0 0 1 6-6z"/><circle cx="6" cy="6" r="2" fill="#fff"/></svg>Ashford Office</div>
      <div class="office-addr" style="font-size:12px;padding-left:3px">210 Oakridge Ave. Suite 120<br>Ashford, MD20000</div>
    </div>
    <div class="office" style="padding:10px 0 8px">
      <div class="office-name" style="font-size:20px"><svg width="12" height="16" viewBox="0 0 12 16"><path fill="var(--pin)" d="M6 0a6 6 0 0 1 6 6c0 4-6 10-6 10S0 10 0 6a6 6 0 0 1 6-6z"/><circle cx="6" cy="6" r="2" fill="#fff"/></svg>Millbrook Office</div>
      <div class="office-addr" style="font-size:12px;padding-left:3px">45 Willow Lane<br>Millbrook, WV20001</div>
    </div>
    <div class="office" style="padding:10px 0 8px">
      <div class="office-name" style="font-size:20px"><svg width="12" height="16" viewBox="0 0 12 16"><path fill="var(--pin)" d="M6 0a6 6 0 0 1 6 6c0 4-6 10-6 10S0 10 0 6a6 6 0 0 1 6-6z"/><circle cx="6" cy="6" r="2" fill="#fff"/></svg>Cedarville Office</div>
      <div class="office-addr" style="font-size:12px;padding-left:3px">980 Harbor Blvd. Suite 300<br>Cedarville, MD20002</div>
    </div>
  </div>

  <svg class="abs" style="left:50px;top:757px" width="66" height="100" viewBox="0 0 44 66" fill="none" stroke="var(--orange)" stroke-width="2">
    <rect x="3" y="3" width="38" height="60" rx="4"/><rect x="9" y="10" width="26" height="14"/>
    <path d="M9 31h6M19 31h6M29 31h6M9 39h6M19 39h6M29 39h6M9 47h6M19 47h6M29 47h6M12 63v-8h20v8"/>
  </svg>
  <p class="abs benefit" style="left:133px;top:757px;width:280px;font-size:20.5px;line-height:1.2">You can now enjoy faster checkout times and greater security with card and</p>
  <div class="abs contactless" style="left:50px;top:870px;font-size:50px;line-height:.98">Contactless<br>Payments</div>

  <div class="abs brand" style="left:52px;top:1035px;font-size:33px"><span class="brand-dot" style="width:30px;height:30px"></span>BMR FOOT CARE</div>

  <div class="abs phone" style="left:48px;top:1160px;font-size:42px">
    <svg width="38" height="38" viewBox="0 0 26 26"><circle cx="13" cy="13" r="13" fill="var(--teal)"/><path fill="#fff" d="M9 6l3 4-2 2c1 2 3 4 5 5l2-2 4 3-2 3c-6 0-12-6-12-12z"/></svg>(555)014-0192
  </div>
  <div class="abs website" style="left:48px;top:1218px;font-size:26px">www.<b>bmrfootcare</b>.com</div>
</section>
<div class="size-label" style="top:2442px">1920 X 1080</div>

</body>
</html>
```